ORV Fashion Design Company Needs a New Web Design, Please Click Me

Designers:

PLEASE NOTE: we only need the web page design, not a fully coded website.

Our brand's name is Orbel Vantra, our signature is print. our style is edgy and chic.

The old website is too messy. here's the address:
www.orvdesign.example.cn

The new website's purpose is to show our brand/design and most importantly, sell products, So it should be a combination of a designer official website and online shopping. I want the whole style to be clean, edgy and pioneer, easy to understand. we need a sophisticated online shopping website.

The reference websites are:
liromapek.example.uk
www.qd-besu.example
talemkorv.example
misolvare.example
pardelunitram.example

Please beat their designs :)

Check out our lasted fashion show to get to know us more.

https://www.videohost.example/watch?v=ZkrpLmWnaYd&spfreload=10

The attachments are our Logo and some 2015 Look Book.
(Please let us know if you want to play with our print in this particular web design, we can send the source file.)
Updates

Designers, we really like the design of helenamardoux.example(we have attached a picture of the website) , Can we get a homepage like that? so the designs you submit will be 3 pages. The first one should be a page that only has Shop/Look. then the shop page, it should be nothing but our product which we will list the categories ourself. And the look page should contain all the info. such as news, about us and designers etc. Thank you all for your hard work, we really enjoyed the designs. Added Monday, November 03, 2014

Target Market(s)

Our target audiences are woman aged from 16-40 who like online shopping

Industry/Entity Type

Online Shopping

Number of Pages Required

3 page

Font styles to use
Serif
Sans Serif
Script

Requirements
Must have
• Designers,
• we really like the design of helenamardoux.example(we have attached a picture of the website) , Can we get a homepage like that? so the designs you submit will be 3 pages. The first one should be a page that only has Shop/Look. then the shop page, it should be nothing but our product which we will list the categories ourself. And the look page should contain all the info. such as news, about us and designers etc. Thank you all for your hard work, we really enjoyed the designs.

```html
<!DOCTYPE html>
<html lang="en">
<head>
<meta charset="utf-8">
<title>ORV Group — Orbel Vantra</title>
<link href="https://fonts.googleapis.com/css2?family=Mulish:wght@300;400&display=swap" rel="stylesheet">
<style>
  :root {
    --paper: #ffffff;
    --ink: #4a4a4a;
    --ink-dark: #222222;
    --muted: #666666;
    --accent: #d0262b;
    --rule: #dcdcdc;
    --icon: #9a9a9a;
    --photo-black: #06080d;
    --photo-deep: #0f2238;
    --photo-mid: #2a4d78;
    --photo-light: #7f9cc0;
    --dress-light: #e9e3da;
    --dress-warm: #c98a5a;
  }
  * { margin: 0; padding: 0; box-sizing: border-box; }
  html, body { width: 1200px; height: 844px; overflow: hidden; background: var(--paper); }
  body { font-family: "Mulish", "Helvetica Neue", Arial, sans-serif; color: var(--ink); position: relative; }

  .sidebar { position: absolute; left: 0; top: 0; width: 600px; height: 844px; }

  .brand { position: absolute; top: 28px; left: 0; width: 600px; text-align: center; }
  .brand-mark { width: 98px; height: 98px; border-radius: 50%; background: var(--accent); margin: 0 auto 10px; }
  .brand-name { font-weight: 400; font-size: 21px; line-height: 19px; color: var(--ink-dark); }
  .brand-name--group { letter-spacing: 3px; }
  .brand-name--label { letter-spacing: 5.2px; }

  .main-nav { position: absolute; top: 219.4px; left: 173px; width: 253px; list-style: none; }
  .main-nav li { height: 43.1px; display: flex; align-items: center; justify-content: center;
    font-size: 14.5px; font-weight: 300; letter-spacing: 0.3px; border-bottom: 1px solid var(--rule); }
  .main-nav li:last-child { border-bottom: none; }
  .main-nav li.is-active { color: var(--accent); }

  .account { position: absolute; top: 715px; left: 0; width: 600px; display: flex; justify-content: center;
    font-size: 12.5px; color: var(--ink-dark); }
  .account span { padding: 0 12px; line-height: 16px; }
  .account span + span { border-left: 1px solid var(--rule); }

  .social { position: absolute; top: 760px; left: 0; width: 600px; display: flex; justify-content: center; gap: 9px; }
  .social span { width: 14px; height: 14px; border-radius: 50%; background: var(--icon); }

  .copyright { position: absolute; top: 797px; left: 0; width: 600px; text-align: center;
    font-size: 13px; font-weight: 300; color: var(--muted); }

  .hero { position: absolute; left: 600px; top: 0; width: 600px; height: 844px;
    background:
      radial-gradient(ellipse 170px 120px at 260px 110px, rgba(214,196,184,0.9) 0%, rgba(214,196,184,0) 100%),
      radial-gradient(ellipse 230px 430px at 330px 560px, rgba(233,227,218,0.95) 0%, rgba(201,138,90,0.45) 55%, rgba(201,138,90,0) 100%),
      radial-gradient(ellipse 120px 300px at 60px 420px, rgba(127,156,192,0.55) 0%, rgba(127,156,192,0) 100%),
      linear-gradient(90deg, var(--photo-mid) 0%, var(--photo-deep) 45%, var(--photo-deep) 70%, var(--photo-black) 100%); }
</style>
</head>
<body>
  <aside class="sidebar">
    <div class="brand">
      <div class="brand-mark"></div>
      <div class="brand-name brand-name--group">ORV GROUP</div>
      <div class="brand-name brand-name--label">ORBEL VANTRA</div>
    </div>

    <ul class="main-nav">
      <li class="is-active">Home</li>
      <li>Online Shopping</li>
      <li>About Us</li>
      <li>Designer</li>
      <li>News</li>
      <li>Member Center</li>
    </ul>

    <div class="account"><span>Login</span><span>Register</span></div>
    <div class="social" aria-label="Social links"><span></span><span></span><span></span></div>
    <p class="copyright">Copyright © 2014 ORV Group.</p>
  </aside>

  <div class="hero" role="img" aria-label="Fashion photograph: model in a colourful feather-print wrap dress against a glossy blue plastic backdrop"></div>
</body>
</html>
```